Relaydeck Tech Company Website B2B Dev Teams Android

We need a completely new website for this tech company. We offer software as a service to companies that have private Android software. Our clients are developers, tech teams, and companies (B2B). We offer a way to keep Android devices updated worldwide without needing a Vantora Shelf account, which suits corporate-owned single-use devices very well.
Our public is technicians (software developers), not people who use smartphones. Most clients run Relaydeck on tablets, drones, point-of-sale devices, etc.
The most used feature is the background update, which requires no user interaction. Our product helps developers keep their private enterprise applications updated. Some references of what developers like to see:
mivorin.example, taskobri.example, flowquenta.example, dravelo.example, kondrix.example
The green doesn't suit it very well. Feel free to change the logo's color (source images .ai .psd attached). The current website has only five small pages. The new one can have five at most (it can have less). The images of the "update strategies" aren't good. It can be replaced by "mock-like" images mimicking how Android interacts with the user. The proportion of the tool icons isn't good. The login and signup forms can be improved a lot.
We hope for a modern website for a tech company with new colors that, at first glance, convey a sense of quality. We want the current standard for SaaS (software as a service) providers' websites.
https://www.relaydeck-app.example/
NO WORDPRESS.
We want it built using Next, Nuxt, or another good static build tool.

Target Market(s)
Android Software Development
Industry/Entity Type
Software
Coding
Coded - Design and coding required
Number of Pages Required
4 page
Requirements
Must have
- We want it built using Next, Nuxt, or another good static build tool

Nice to have
- Android message notification mockups instead screenshots

Should not have
- wordpress

```html
<!DOCTYPE html>
<html lang="en">
<head>
<meta charset="UTF-8">
<title>Relaydeck – Login</title>
<link href="https://fonts.googleapis.com/css2?family=Poppins:wght@400;500;600&display=swap" rel="stylesheet">
<style>
:root{
  --bg:#f2f2f2;
  --ink:#111111;
  --navy:#0c1466;
  --brand:#0b3a8c;
  --brand-2:#0b5bb5;
  --band:#dfe9f1;
  --field:#efefef;
  --line:#d6d6d6;
  --white:#ffffff;
  --muted:#555555;
}
*{box-sizing:border-box;margin:0;padding:0}
html,body{width:1104px;height:1200px;overflow:hidden}
body{background:var(--bg);font-family:'Poppins',sans-serif;color:var(--ink);position:relative}
.abs{position:absolute}

/* header */
.logo{font-weight:600;color:var(--navy);letter-spacing:-0.5px}
.site-header .logo{left:34px;top:24px;font-size:30px}
.main-nav{left:376px;top:27px;width:360px;height:36px;border-radius:18px;background:#f7f7f7;display:flex;align-items:center;justify-content:space-around;padding:0 12px;font-size:11.5px}
.btn{display:flex;align-items:center;justify-content:center;gap:6px;border-radius:20px;font-size:10.5px;font-weight:600;text-transform:uppercase}
.btn-outline{border:1.3px solid var(--navy);color:var(--navy)}
.btn-solid{background:linear-gradient(90deg,var(--brand),var(--brand-2));color:var(--white)}
.header-login{left:883px;top:25px;width:89px;height:38px}
.header-signup{left:984px;top:25px;width:89px;height:38px}

/* breadcrumb */
.breadcrumb{left:0;top:80px;width:1104px;height:39px;background:var(--band);display:flex;align-items:center;padding-left:34px;font-size:11px;gap:8px}
.breadcrumb .current{color:var(--brand);font-weight:600}

/* login card */
.login-card{left:162px;top:185px;width:780px;height:538px;background:var(--white);border:1px solid #e2e2e2;border-radius:20px;overflow:hidden}
.login-visual{position:absolute;left:0;top:0;width:337px;height:538px;border-radius:20px;background:linear-gradient(160deg,#5f6c80 0%,#8a7060 45%,#9a5a33 75%,#6e3c1f 100%)}
.login-form{position:absolute;left:370px;top:0;width:378px}
.login-title{position:absolute;top:118px;font-size:28px;font-weight:600}
.field{position:absolute;left:0;width:378px;height:35px;background:var(--field);border-radius:6px;font-size:11px;display:flex;align-items:center;padding-left:20px;color:#222}
.field-email{top:175px}
.field-password{top:230px}
.form-links{position:absolute;top:277px;width:378px;display:flex;justify-content:space-between;font-size:8.5px}
.form-links a{color:var(--brand);font-weight:600;text-decoration:underline}
.captcha{position:absolute;top:308px;width:204px;height:48px;background:#f9f9f9;border:1px solid #d3d3d3;border-radius:3px;display:flex;align-items:center;padding:0 8px;font-size:10.5px}
.captcha .box{width:22px;height:22px;border:2px solid #c1c1c1;border-radius:2px;background:#fff;margin-right:10px}
.captcha .mark{margin-left:auto;text-align:center;font-size:5.5px;color:#666;line-height:1.4}
.captcha .mark i{display:block;width:16px;height:16px;border-radius:50%;background:#4a8af4;margin:0 auto 2px}
.sign-in{position:absolute;top:380px;width:119px;height:38px;border:1.2px solid var(--ink);border-radius:20px;font-size:10px;font-weight:600;display:flex;align-items:center;justify-content:center}

/* footer */
.footer-rule{left:0;top:810px;width:1104px;height:1px;background:var(--line)}
.site-footer .logo{left:129px;top:895px;font-size:38px}
.footer-tagline{left:129px;top:970px;width:270px;font-size:12px;line-height:20px;color:#222}
.footer-login{left:129px;top:1045px;width:89px;height:38px}
.footer-signup{left:230px;top:1045px;width:89px;height:38px;background:var(--navy)}
.footer-col h3{font-size:17px;font-weight:500;color:var(--navy);margin-bottom:12px}
.footer-col ul{list-style:none}
.footer-col li{font-size:15px;color:#333;height:34px;display:flex;align-items:center;gap:12px}
.footer-col li::before{content:"›";font-size:16px;color:#333;width:8px}
.col-quick{left:448px;top:895px}
.col-features{left:610px;top:895px}
.col-other{left:810px;top:895px}
.to-top{left:1050px;top:1082px;width:26px;height:26px;border-radius:5px;background:#e4e4e4;display:flex;align-items:center;justify-content:center}
.bottom-bar{left:0;top:1153px;width:1104px;height:47px;background:var(--navy)}
.social{position:absolute;top:10px;width:26px;height:26px;border-radius:50%;border:1px solid #8a90c8}
.social.active{background:var(--white)}
</style>
</head>
<body>

<header class="site-header">
  <div class="abs logo">Relaydeck</div>
  <nav class="abs main-nav"><span>HOME</span><span>FEATURES</span><span>PRICING</span><span>DOCS</span><span>STATUS</span></nav>
  <a class="abs btn btn-outline header-login">
    <svg width="14" height="14" viewBox="0 0 16 16" fill="none" stroke="currentColor" stroke-width="1.4"><path d="M9 2h4v12H9"/><path d="M2 8h8M7 5l3 3-3 3"/></svg>Login</a>
  <a class="abs btn btn-solid header-signup">Sign up</a>
</header>

<div class="abs breadcrumb"><span>Home</span><span>»</span><span class="current">Login</span></div>

<main class="abs login-card">
  <div class="login-visual" role="img" aria-label="Photo of hands holding a smartphone with floating app interface cards"></div>
  <div class="login-form">
    <h1 class="login-title">Login</h1>
    <div class="field field-email">Enter Your Email Address*</div>
    <div class="field field-password">Password*</div>
    <div class="form-links"><span>New Customer? <a>Create Account</a></span><a>Forgot Your Password?</a></div>
    <div class="captcha"><span class="box"></span>I'm not a robot<span class="mark"><i></i>HumanCheck<br>Privacy · Terms</span></div>
    <div class="sign-in">SIGN IN</div>
  </div>
</main>

<div class="abs footer-rule"></div>

<footer class="site-footer">
  <div class="abs logo">Relaydeck</div>
  <p class="abs footer-tagline">Keep your private android application self-updated without any third-party process.</p>
  <a class="abs btn btn-outline footer-login">
    <svg width="14" height="14" viewBox="0 0 16 16" fill="none" stroke="currentColor" stroke-width="1.4"><path d="M9 2h4v12H9"/><path d="M2 8h8M7 5l3 3-3 3"/></svg>Login</a>
  <a class="abs btn btn-solid footer-signup">Sign up</a>

  <div class="abs footer-col col-quick"><h3>Quick Links</h3><ul><li>Home</li><li>Features</li><li>Pricing</li><li>Docs</li><li>Status</li></ul></div>
  <div class="abs footer-col col-features"><h3>Our Features</h3><ul><li>Host your apk</li><li>Devices Enrollment</li><li>Manage Versions</li><li>Track Installations</li><li>View All</li></ul></div>
  <div class="abs footer-col col-other"><h3>Other Links</h3><ul><li>Terms &amp; Conditions</li><li>Privacy Policy</li><li>Sitemap</li><li>Contact Us</li></ul></div>

  <div class="abs to-top"><svg width="10" height="12" viewBox="0 0 10 12" fill="none" stroke="#333" stroke-width="1.2"><path d="M5 11V1M1 5l4-4 4 4"/></svg></div>

  <div class="abs bottom-bar">
    <span class="social" style="left:843px"></span>
    <span class="social active" style="left:877px"></span>
    <span class="social" style="left:912px"></span>
    <span class="social" style="left:947px"></span>
  </div>
</footer>

</body>
</html>
```